New Business card design to reflect rebrand

I would like a business card design with a good base colour for our new logo and also a placeholder for a profile pic of the card holder. the design needs to be editable to the point that we can easily change the picture of the person and use that design for printmerlo etc. we are looking at a metalic finish business card so will need a good base colour to bring out the finish.

Target Market(s)

prospective customers

Industry/Entity Type

Business

Contact Information for Business Card

I would like one editable design that we can change the name of the card holder and profile picture. The design need to be in a format that be send to printmerlo etc.

Our address is Fenwick Lodge, Copse Lane, Elmbury Green, GU14 3TP Tel no. 01483 556172

Requirements
Must have
• place holder for a profile pic for the card holder. in AI or preferably PSD format

```html
<!DOCTYPE html>
<html lang="en">
<head>
<meta charset="utf-8">
<title>Corvane Workplace Services – Business Card</title>
<link rel="stylesheet" href="https://fonts.googleapis.com/css2?family=Open+Sans:wght@400;600;700&display=swap">
<style>
  :root {
    --page-bg: #ece9e6;
    --card-orange: #e8620e;
    --card-orange-deep: #d55408;
    --card-white: #f7f7f6;
    --brand-slate: #3f5169;
    --brand-orange: #e8620e;
    --text-light: #ffffff;
    --photo-top: #c9c4bd;
    --photo-bottom: #2a3146;
  }
  * { box-sizing: border-box; margin: 0; padding: 0; }
  html, body { width: 1200px; height: 900px; overflow: hidden; }
  body {
    position: relative;
    background: var(--page-bg);
    font-family: "Open Sans", Arial, sans-serif;
  }
  .card {
    position: absolute;
    border-radius: 2px;
    box-shadow: 0 6px 18px rgba(0, 0, 0, 0.18);
    overflow: hidden;
  }
  /* Front */
  .card-front {
    left: 238px; top: 60px; width: 555px; height: 345px;
    background: linear-gradient(135deg, var(--card-orange) 0%, var(--card-orange-deep) 100%);
    color: var(--text-light);
  }
  .front-brand {
    position: absolute; left: 34px; top: 48px;
    display: flex; align-items: center; gap: 12px;
  }
  .brand-square {
    width: 26px; height: 26px; background: var(--brand-slate);
  }
  .front-brand .brand-name {
    font-size: 38px; font-weight: 700; color: var(--brand-slate); letter-spacing: 1px;
  }
  .holder-name {
    position: absolute; left: 33px; top: 163px;
    font-size: 20px; font-weight: 700;
  }
  .contact-list {
    position: absolute; left: 33px; top: 202px;
    list-style: none; font-size: 14px; line-height: 24px;
  }
  .contact-list li { display: flex; align-items: center; gap: 8px; }
  .contact-list svg { width: 11px; height: 11px; fill: var(--text-light); }
  .postal-address {
    position: absolute; left: 34px; top: 258px;
    font-size: 14px; line-height: 22px; font-style: normal;
  }
  .profile-photo {
    position: absolute; right: 0; top: 0; width: 230px; height: 345px;
    background: linear-gradient(180deg, var(--photo-top) 0%, #8a8580 40%, var(--photo-bottom) 100%);
  }
  /* Back */
  .card-back {
    left: 457px; top: 518px; width: 560px; height: 344px;
    background: var(--card-white);
  }
  .back-brand {
    position: absolute; left: 0; right: 0; top: 112px;
    display: flex; flex-direction: column; align-items: center; gap: 10px;
  }
  .back-brand .brand-square { width: 34px; height: 34px; background: var(--brand-orange); }
  .back-brand .brand-name {
    font-size: 40px; font-weight: 700; color: var(--brand-slate); letter-spacing: 3px;
    text-transform: uppercase; line-height: 1.05; text-align: center;
  }
  .back-brand .brand-name span { display: block; font-size: 20px; letter-spacing: 4px; margin-top: 4px; }
</style>
</head>
<body>
  <section class="card card-front" aria-label="Business card front">
    <div class="front-brand">
      <span class="brand-square"></span>
      <span class="brand-name">Corvane</span>
    </div>
    <h1 class="holder-name">Adam Pryce</h1>
    <ul class="contact-list">
      <li>
        <svg viewBox="0 0 24 24" aria-hidden="true"><path d="M6.6 10.8a15.2 15.2 0 0 0 6.6 6.6l2.2-2.2a1 1 0 0 1 1-.25 11.4 11.4 0 0 0 3.6.57 1 1 0 0 1 1 1V20a1 1 0 0 1-1 1A17 17 0 0 1 3 4a1 1 0 0 1 1-1h3.5a1 1 0 0 1 1 1c0 1.25.2 2.45.57 3.6a1 1 0 0 1-.25 1z"/></svg>
        01483 556172
      </li>
      <li>
        <svg viewBox="0 0 24 24" aria-hidden="true"><path d="M2 5h20v14H2z"/><path d="M3 6l9 7 9-7" fill="none" stroke="#d85a0b" stroke-width="2"/></svg>
        info@corvane.com
      </li>
    </ul>
    <address class="postal-address">Fenwick Lodge, Copse Lane,<br>Elmbury Green, GU14 3TP</address>
    <div class="profile-photo" role="img" aria-label="Profile photo of the card holder"></div>
  </section>

  <section class="card card-back" aria-label="Business card back">
    <div class="back-brand">
      <span class="brand-square"></span>
      <p class="brand-name">Corvane<span>Workplace Services</span></p>
    </div>
  </section>
</body>
</html>
```